Pellowar

We need logo and wesbsite for a software development company based out of Hyderabad, India focused on startups and mid sized companies focused on build a new software products in USA and Europe countires.

Target Market(s)

startup and midsized companies in teh USA and Europe for software product development.

Industry/Entity Type

software development

Coding

Coded - Design and coding required

Number of Pages Required

5+ page

Requirements
Must have
• latest design concepts and very elegant
Nice to have
• each page should have images that reflects the content
Should not have
• too many colors

```html
<!DOCTYPE html>
<html lang="en">
<head>
<meta charset="utf-8">
<title>Pellowar — Software Development</title>
<link rel="stylesheet" href="https://fonts.googleapis.com/css2?family=Audiowide&family=Roboto:wght@400;500;700&display=swap">
<style>
:root{
  --blue:#1e7be6;
  --sky:#29a3f0;
  --violet:#7a14d8;
  --indigo:#4a2fe0;
  --ink:#15141f;
  --night:#12111b;
  --text:#5b5b66;
  --white:#ffffff;
  --grad:linear-gradient(90deg,#1b6ff0,#7b15dc);
}
*{box-sizing:border-box;margin:0;padding:0}
html,body{width:1200px;height:4277px;overflow:hidden}
body{position:relative;background:var(--white);font-family:"Roboto",sans-serif;color:var(--text)}
.display{font-family:"Audiowide",sans-serif;text-transform:uppercase;color:var(--ink);letter-spacing:1px}
.abs{position:absolute}
.btn{position:absolute;display:flex;align-items:center;justify-content:center;gap:8px;background:var(--grad);color:var(--white);border-radius:24px;font-weight:700;font-size:14px;text-transform:uppercase;letter-spacing:.3px}
.btn .arrow{width:14px;height:14px;border-radius:50%;background:var(--white);display:inline-flex;align-items:center;justify-content:center}
.btn .arrow::after{content:"";border-left:5px solid #4b3be0;border-top:4px solid transparent;border-bottom:4px solid transparent;margin-left:2px}

/* hero */
.hero{left:0;top:0;width:1200px;height:730px;clip-path:polygon(0 0,100% 0,100% 730px,0 605px);
  background:radial-gradient(ellipse at 70% 45%,#3a4f78 0%,#1e2a45 45%,#0e1526 100%)}
.brand{display:flex;align-items:center;gap:12px;font-family:"Audiowide",sans-serif;color:var(--white);font-size:24px;text-transform:uppercase}
.brand .mark{width:36px;height:36px;border-radius:50%;background:var(--indigo)}
.nav{left:418px;top:44px;display:flex;gap:23px;font-size:14px;font-weight:500;color:var(--white)}
.nav .active{color:var(--sky)}
.hero-title{position:absolute;left:110px;top:205px;font-size:48px;line-height:52px;color:var(--white)}
.hero-intro{position:absolute;left:110px;top:325px;width:410px;color:var(--white);font-size:16px;line-height:26px;font-weight:500}
.dots{left:1142px;top:328px;display:flex;flex-direction:column;gap:11px}
.dots span{width:13px;height:13px;border-radius:50%;border:2px solid var(--white)}
.dots span.on{background:radial-gradient(circle,var(--white) 35%,transparent 40%)}

/* hexagon photos */
.hex{clip-path:polygon(50% 0,100% 25%,100% 75%,50% 100%,0 75%,0 25%)}
.hex-frame{position:absolute;background:linear-gradient(180deg,#27a6f2 0%,#3a5fe6 50%,#7a14d8 100%)}
.hex-photo{position:absolute;left:34px;top:38px;right:34px;bottom:38px}

.section-copy{font-size:14px;line-height:24px;color:var(--text)}

/* product */
.product{left:0;top:1203px;width:1200px;height:802px;background:radial-gradient(ellipse at 50% 55%,#201e33 0%,var(--night) 70%);
  clip-path:polygon(0 120px,100% 0,100% 802px,0 678px)}
.role{position:absolute;display:flex;align-items:center;gap:18px;color:var(--white);font-weight:700;font-size:19px;line-height:26px}
.role .badge{width:104px;height:104px;background:var(--white);display:flex;align-items:center;justify-content:center}
.role .icon{width:54px;height:54px;border-radius:50%;background:linear-gradient(135deg,#cfe3fb,#d9c9f6)}
.core{left:478px;top:1525px;width:244px;height:244px;border-radius:50%;background:#1a1928;display:flex;align-items:center;justify-content:center;font-family:"Audiowide",sans-serif;font-size:30px;color:var(--white);text-transform:uppercase}

/* process */
.process{left:0;top:2523px;width:1200px;height:681px;background:linear-gradient(100deg,#1c61d8 0%,#4a3ae0 50%,#6d0fc8 100%);
  clip-path:polygon(0 117px,100% 0,100% 681px,0 556px)}
.step{position:absolute;width:320px;text-align:center;color:var(--white)}
.step .num{position:relative;height:130px}
.step .digit{position:absolute;left:50px;top:0;font-family:"Audiowide",sans-serif;font-size:118px;line-height:130px;color:transparent;-webkit-text-stroke:3px var(--white)}
.step .ring{position:absolute;left:122px;top:2px;width:124px;height:124px;border-radius:50%;border:4px solid var(--white);display:flex;align-items:center;justify-content:center}
.step .ring i{width:96px;height:96px;border-radius:50%;background:var(--white);display:flex;align-items:center;justify-content:center}
.step .ring i b{width:62px;height:62px;border-radius:50%;background:linear-gradient(135deg,#9cc8f6,#9f7de8)}
.step h3{margin-top:26px;font-size:18px;font-weight:700}
.step p{margin-top:16px;font-size:14px;line-height:23px;color:#e9e6ff}

/* cases */
.card{position:absolute;top:3371px;width:310px;height:409px;background:var(--white);box-shadow:0 4px 22px rgba(20,20,40,.12)}
.card .img{height:211px;background:linear-gradient(135deg,#8d8a86,#4d5560)}
.card .date{position:absolute;left:18px;top:200px;height:27px;padding:0 14px;background:var(--grad);color:var(--white);font-size:13px;display:flex;align-items:center}
.card h4{margin:42px 21px 0;font-size:16px;color:var(--ink);font-weight:700}
.card p{margin:12px 21px 0;font-size:13px;line-height:22px}
.card .more{margin:14px 21px 0;font-size:14px;font-weight:700;color:var(--blue);display:flex;align-items:center;gap:6px}
.card .more::after{content:"";width:12px;height:12px;border-radius:50%;background:var(--blue)}

/* footer */
.footer{left:0;top:3904px;width:1200px;height:373px;background:var(--night);clip-path:polygon(0 72px,100% 0,100% 100%,0 100%)}
.fcol{position:absolute;top:3966px;color:var(--white)}
.fcol h5{font-size:16px;font-weight:700;margin-bottom:18px}
.fcol li{list-style:none;font-size:13px;line-height:26px;color:#d9d9e2}
.contact-item{display:flex;gap:12px;margin-bottom:14px;font-size:13px;line-height:19px;color:#d9d9e2}
.contact-item b{display:block;color:var(--white);font-size:12px}
.contact-item svg{flex:none;margin-top:3px}
.socials{left:158px;top:4079px;display:flex;gap:10px}
.socials span{width:31px;height:31px;border-radius:50%;border:1.5px solid #cfcfd8}
.copy{left:0;top:4226px;width:1200px;text-align:center;color:var(--white);font-size:14px}
.totop{left:1107px;top:4182px;width:36px;height:36px;border-radius:50%;background:var(--grad);display:flex;align-items:center;justify-content:center}
</style>
</head>
<body>

<!-- hero -->
<section class="abs hero" role="img" aria-label="Photo of a developer working on a tablet with code overlay"></section>
<div class="abs brand" style="left:113px;top:36px"><span class="mark"></span>Pellowar</div>
<nav class="abs nav"><span class="active">Home</span><span>About Us</span><span>Build Your Product</span><span>Build Your Team</span><span>Case Study</span></nav>
<div class="btn" style="left:963px;top:37px;width:126px;height:38px;text-transform:none;font-size:15px">Contact</div>
<h1 class="display hero-title">Software<br>Development</h1>
<p class="hero-intro">Teams are the essence of every business. They can create wonders if built with perfection.</p>
<div class="btn" style="left:110px;top:403px;width:197px;height:45px;font-variant:small-caps;text-transform:none;font-size:16px">Get Started <span class="arrow"></span></div>
<div class="abs dots"><span></span><span class="on"></span><span></span></div>

<!-- about -->
<div class="hex-frame hex" style="left:111px;top:727px;width:404px;height:465px">
  <div class="hex-photo hex" role="img" aria-label="Photo of a smiling man working on a laptop" style="background:linear-gradient(135deg,#e6ecf2,#8fa9c4)"></div>
</div>
<h2 class="abs display" style="left:613px;top:766px;font-size:46px">About Us</h2>
<div class="abs section-copy" style="left:614px;top:842px;width:475px;text-align:justify">
  <p>Teams are the essence of every business. They can create wonders if built with perfection.</p>
  <p style="margin-top:12px">We are a group of entrepreneurs, technocrats, software architects, and delivery heads who have come together to serve startups, product companies, and enterprises with their product development. We are prompt in understanding your product and help design, build, maintain and operate your product. Pellowar quickly set up a team of UX experts, Business Analysts, Developers and QA resources to build the best team to deliver the product.</p>
</div>
<div class="btn" style="left:614px;top:1099px;width:193px;height:47px">Learn More <span class="arrow"></span></div>

<!-- build your product -->
<section class="abs product"></section>
<svg class="abs" style="left:0;top:1203px" width="1200" height="802" aria-hidden="true">
  <g stroke="#3a3850" stroke-width="1" fill="none">
    <line x1="398" y1="296" x2="600" y2="444"/><line x1="802" y1="296" x2="600" y2="444"/>
    <line x1="347" y1="445" x2="600" y2="444"/><line x1="850" y1="445" x2="600" y2="444"/>
    <line x1="398" y1="598" x2="600" y2="444"/><line x1="802" y1="598" x2="600" y2="444"/>
  </g>
</svg>
<h2 class="abs display" style="left:0;width:1200px;text-align:center;top:1345px;font-size:46px;color:var(--white)">Build Your Product</h2>
<div class="abs core">Pellowar</div>

<div class="role" style="right:750px;top:1447px">Project Manager<span class="badge hex"><span class="icon" role="img" aria-label="Project manager icon"></span></span></div>
<div class="role" style="left:750px;top:1447px"><span class="badge hex"><span class="icon" role="img" aria-label="Developer icon"></span></span>Developers</div>
<div class="role" style="right:801px;top:1596px">Business analyst<span class="badge hex"><span class="icon" role="img" aria-label="Business analyst icon"></span></span></div>
<div class="role" style="left:798px;top:1596px"><span class="badge hex"><span class="icon" role="img" aria-label="Tester icon"></span></span>Testers</div>
<div class="role" style="right:750px;top:1749px">Team Lead<span class="badge hex"><span class="icon" role="img" aria-label="Team lead icon"></span></span></div>
<div class="role" style="left:750px;top:1749px"><span class="badge hex"><span class="icon" role="img" aria-label="Writer icon"></span></span>Technical/Content<br>Writers</div>

<!-- build your team -->
<h2 class="abs display" style="left:111px;top:2088px;font-size:46px">Build Your Team</h2>
<div class="abs section-copy" style="left:111px;top:2162px;width:480px">
  <p>Break free from traditional recruiting with us. At Pellowar, we help you achieve the right organizational matrix with rockstars who can take your business to the next level.</p>
  <p style="margin-top:14px">We have spent years trying to innovate and improve the process of hiring talented individuals who can take businesses to the next level. We ensure that the workforce we employ for your organization is highly productive and takes you to the golden standards of heights.</p>
</div>
<div class="btn" style="left:113px;top:2379px;width:192px;height:46px">Learn More <span class="arrow"></span></div>
<div class="hex-frame hex" style="left:669px;top:2029px;width:405px;height:464px">
  <div class="hex-photo hex" role="img" aria-label="Photo of a team gathered around a laptop" style="background:linear-gradient(135deg,#dfe6ee,#7d93ad)"></div>
</div>

<!-- process -->
<section class="abs process"></section>
<h2 class="abs display" style="left:0;width:1200px;text-align:center;top:2660px;font-size:46px;color:var(--white)">Our Process</h2>
<div class="step" style="left:106px;top:2752px">
  <div class="num"><span class="digit">1</span><span class="ring"><i role="img" aria-label="Aptitude test icon"><b></b></i></span></div>
  <h3>Pass cognitive aptitude test</h3>
  <p>Accepting job applications from the entire world means every role on Tallyway receives thousands of applications. We find that the most reliable way to shortlist the very best candidates is by objectively</p>
</div>
<div class="step" style="left:440px;top:2752px">
  <div class="num"><span class="digit">2</span><span class="ring"><i role="img" aria-label="Language test icon"><b></b></i></span></div>
  <h3>Pass English proficiency test</h3>
  <p>Someday, technological advancements will make it possible for teams to collaborate without sharing a common language. Until then, English language skills are necessary for all positions advertised on Tallyway.</p>
</div>
<div class="step" style="left:773px;top:2752px">
  <div class="num"><span class="digit">3</span><span class="ring"><i role="img" aria-label="Job skills icon"><b></b></i></span></div>
  <h3>Prove real-world job skills</h3>
  <p>Of course, there's much more to being a great worker than intelligence and language skills. The next step is to complete a real-world job assignment which has been curated specifically for the role</p>
</div>

<!-- case study -->
<h2 class="abs display" style="left:0;width:1200px;text-align:center;top:3222px;font-size:46px">Case Study</h2>
<p class="abs" style="left:240px;width:720px;text-align:center;top:3289px;font-size:14px;line-height:24px">Many business owners have great ideas but no experience with the actual product. Once you have an idea in mind, you will require software development aid at some point</p>

<article class="card" style="left:111px">
  <div class="img" role="img" aria-label="Photo of an empty modern office with sunlight"></div>
  <span class="date">Jan 2, 2022</span>
  <h4>What is GradPathway?</h4>
  <p>The GradPathway platform simplifies the process of finding and applying to graduate schools.</p>
  <div class="more">READ MORE</div>
</article>
<article class="card" style="left:445px">
  <div class="img" role="img" aria-label="Photo of colleagues meeting at a table" style="background:linear-gradient(135deg,#c9ccd1,#5d6470)"></div>
  <span class="date">Jan 2, 2022</span>
  <h4>Your Graduate Journey's Tools</h4>
  <p>You will have access to innovative options like 360 assessment and bookmarking once you create your account,</p>
  <div class="more">READ MORE</div>
</article>
<article class="card" style="left:780px">
  <div class="img" role="img" aria-label="Photo of two professionals discussing work" style="background:linear-gradient(135deg,#b7c4d2,#4f6278)"></div>
  <span class="date">Jan 2, 2022</span>
  <h4>Make Your Admissions Process...</h4>
  <p>'Your Schedule' is a customizable tool that generates a customized timetable based on your anticipated start date.</p>
  <div class="more">READ MORE</div>
</article>

<!-- footer -->
<footer class="abs footer"></footer>
<div class="abs brand" style="left:116px;top:4021px"><span class="mark"></span>Pellowar</div>
<div class="abs socials"><span></span><span></span><span></span><span></span></div>

<div class="fcol" style="left:448px">
  <h5>Quick Links</h5>
  <ul><li>Home</li><li>About Us</li><li>Build your product</li><li>Build your team</li><li>Case study</li><li>Contact</li></ul>
</div>
<div class="fcol" style="left:644px">
  <h5>About Company</h5>
  <ul><li>Legal Information</li><li>Terms &amp; Condition</li><li>Privacy Policy</li><li>Support</li><li>Site Map</li></ul>
</div>
<div class="fcol" style="left:853px;width:260px">
  <h5>Contact Us</h5>
  <div class="contact-item"><svg width="14" height="14" viewBox="0 0 24 24"><path fill="#2f86f0" d="M6.6 10.8a15 15 0 0 0 6.6 6.6l2.2-2.2a1 1 0 0 1 1-.25 11 11 0 0 0 3.6.6 1 1 0 0 1 1 1V20a1 1 0 0 1-1 1A17 17 0 0 1 3 4a1 1 0 0 1 1-1h3.5a1 1 0 0 1 1 1 11 11 0 0 0 .6 3.6 1 1 0 0 1-.25 1z"/></svg><div><b>Phone</b>+1 (555) 014 2290</div></div>
  <div class="contact-item"><svg width="16" height="12" viewBox="0 0 16 12"><rect width="16" height="12" rx="1" fill="#5a3fe0"/><path d="M1 1l7 5 7-5" stroke="#fff" stroke-width="1.2" fill="none"/></svg><div><b>Email</b>admin@pellowar.example</div></div>
  <div class="contact-item"><svg width="12" height="16" viewBox="0 0 12 16"><path fill="#2f86f0" d="M6 0a6 6 0 0 0-6 6c0 4.5 6 10 6 10s6-5.5 6-10a6 6 0 0 0-6-6zm0 8.2A2.2 2.2 0 1 1 6 3.8a2.2 2.2 0 0 1 0 4.4z"/></svg><div><b>Location</b>2011 Lorem ipsum dolor sit amet,<br>consectetur adipiscing</div></div>
</div>
<div class="abs totop"><svg width="14" height="10" viewBox="0 0 14 10"><path d="M2 8l5-5 5 5" stroke="#fff" stroke-width="2" fill="none"/></svg></div>
<p class="abs copy">2022 Copyright - Pellowar | All Rights Reserved</p>

</body>
</html>
```